Vantor Wear and Fuel is looking for a Clothing/Supplement Online Store Website!

Must be convenient, and user friendly, with vibrant colors that catch the eye!

Target Market(s)

Athletes, and Fashion Customers

Industry/Entity Type

Fitness

Coding

Coded - Design and coding required

Number of Pages Required

3 page

Font styles to use
Decorative

Colors

Designer to choose colors to be used in the design.

Requirements
Must have
• Somewhere to feature products, features to promote discounts and make announcements.
Nice to have
• My logos on each page

```html
<!DOCTYPE html>
<html lang="en">
<head>
<meta charset="utf-8">
<title>Vantor Wear and Fuel – Online Store</title>
<link href="https://fonts.googleapis.com/css2?family=IBM+Plex+Sans:wght@400;500;600;700&display=swap" rel="stylesheet">
<style>
:root{
  --orange:#f07c1b;
  --ink:#222;
  --text:#555;
  --muted:#999;
  --hero:#4d4a8e;
  --soft:#f3eff0;
  --dark:#2e2e2e;
  --strip:#4b4b4b;
  --strip-mid:#5a5a5a;
  --cream:#f6f1dc;
  --coral:#f28a80;
  --coral-deep:#ee6f66;
  --red:#b30f0f;
  --grey:#4a4a4a;
  --social:#1d6fd8;
  --navy:#12205a;
}
*{box-sizing:border-box;margin:0;padding:0}
html,body{width:1200px;height:4721px;overflow:hidden}
body{position:relative;font-family:"IBM Plex Sans",Arial,sans-serif;color:var(--ink);background:#fff}
.abs{position:absolute}
.btn{position:absolute;background:var(--orange);color:#fff;font-weight:700;font-size:14px;text-transform:uppercase;display:flex;align-items:center;justify-content:center;letter-spacing:.3px}
.btn-ghost{background:transparent;border:2px solid var(--orange);color:var(--orange)}
.ph{position:absolute}
.divider{position:absolute;left:575px;width:50px;height:5px;background:#bdbdbd}
.section-title{position:absolute;left:0;width:1200px;text-align:center;font-weight:700;font-size:28px;letter-spacing:.5px;text-transform:uppercase}
.circle{display:inline-block;width:25px;height:25px;border-radius:50%}

.brand{position:absolute;font-weight:700;text-transform:uppercase;letter-spacing:2px;color:var(--ink);display:flex;align-items:center;gap:10px}
.brand .mark{width:22px;height:22px;background:var(--ink)}
.follow{left:510px;top:32px;display:flex;align-items:center;gap:8px;font-size:11px}
.search{left:720px;top:28px;width:180px;height:37px;border:1px solid #bbb;font-size:10px;padding:0 12px;display:flex;align-items:center;justify-content:space-between}
.nav{left:452px;top:90px;display:flex;gap:32px;font-size:13px;font-weight:500}
.nav .active{color:var(--orange);border-bottom:2px solid var(--orange);padding-bottom:2px}

.hero{left:0;top:126px;width:1200px;height:605px;background:var(--hero)}
.hero-arrow{position:absolute;top:410px;width:34px;height:36px;background:#fff;display:flex;align-items:center;justify-content:center}
.hero-title{left:0;width:1200px;text-align:center;color:#fff;font-weight:600}

.filter{position:absolute;top:873px;height:36px;font-size:13px;font-weight:600;border:1px solid #999;display:flex;align-items:center;justify-content:center}
.prod-name{position:absolute;width:220px;text-align:center;font-size:14px;font-weight:700}
.prod-price{position:absolute;width:220px;text-align:center;font-size:19px;font-weight:700}
.prod-price s{font-size:13px;color:var(--muted);font-weight:400;margin-left:4px}
.tag{position:absolute;width:70px;height:24px;border:1px solid var(--orange);color:var(--orange);font-size:11px;font-weight:600;display:flex;align-items:center;justify-content:center}
.card{position:absolute;background:#fff;box-shadow:0 4px 20px rgba(0,0,0,.08)}

.promo-title{position:absolute;color:#fff;font-size:32px;font-weight:600}
.promo-rule{position:absolute;width:45px;height:3px;background:#fff}
.promo-text{position:absolute;color:#fff;font-size:17px;line-height:23px;width:220px}

.deal{position:absolute;top:2050px;width:460px;height:312px;color:#fff;text-align:center}
.deal h3{position:absolute;top:42px;width:100%;font-size:41px;font-weight:700}
.deal p{position:absolute;top:110px;left:80px;width:300px;font-size:14px;line-height:20px}
.code{position:absolute;top:168px;left:150px;width:160px;height:38px;border:2px solid var(--orange);color:var(--orange);font-size:14px;font-weight:700;display:flex;align-items:center;justify-content:center}

.voucher{left:0;top:3023px;width:1200px;height:515px;background:linear-gradient(90deg,var(--cream) 0%,var(--cream) 60%,#f4c7b6 76%,var(--coral) 84%,var(--coral) 100%);overflow:hidden}
.voucher-frame{position:absolute;left:245px;top:195px;width:370px;height:275px;border:5px solid var(--coral)}
.voucher-amount{position:absolute;left:245px;top:250px;width:370px;text-align:center;color:var(--coral-deep);font-weight:400}
.voucher-side{position:absolute;transform:rotate(-90deg);transform-origin:0 0;color:#fff;white-space:nowrap}

.blog{position:absolute;top:3718px;width:293px;height:407px;border:2px solid #ddd;background:#fff}
.blog .date{position:absolute;left:26px;top:240px;font-size:13px}
.blog h4{position:absolute;left:26px;top:262px;font-size:14px;font-weight:700}
.blog p{position:absolute;left:26px;top:290px;width:230px;font-size:13px;line-height:19px;color:var(--text)}
.blog a{position:absolute;left:26px;top:366px;font-size:12px;font-weight:700;color:var(--orange)}

.strip h5{position:absolute;color:#fff;font-size:13px;font-weight:700}
.strip p{position:absolute;color:#bbb;font-size:12px;line-height:16px;width:150px}
.foot-head{position:absolute;color:#fff;font-size:15px;font-weight:700}
.foot-list{position:absolute;color:#fff;font-size:13px;line-height:24px;list-style:none}
.contact-row{position:absolute;left:582px;display:flex;gap:12px;color:#fff;font-size:13px;line-height:18px}
.contact-row .dot{width:28px;height:28px;border-radius:50%;background:#fff;display:flex;align-items:center;justify-content:center;flex:none}
.field{position:absolute;left:810px;width:256px;height:38px;background:#fff;font-size:12px;color:#555;padding-left:12px;display:flex;align-items:center}
</style>
</head>
<body>

<header>
  <div class="brand" style="left:130px;top:58px;font-size:26px"><span class="mark"></span>Vantor</div>
  <div class="abs follow">FOLLOW US
    <span class="circle" style="background:var(--social)"></span>
    <span class="circle" style="background:var(--social)"></span>
    <span class="circle" style="background:var(--navy)"></span>
  </div>
  <div class="abs search"><span>SEARCH FOR ITEMS</span>
    <svg width="12" height="12" viewBox="0 0 12 12"><circle cx="5" cy="5" r="3.5" fill="none" stroke="#222" stroke-width="1.6"/><line x1="7.5" y1="7.5" x2="11" y2="11" stroke="#222" stroke-width="1.6"/></svg>
  </div>
  <svg class="abs" style="left:975px;top:32px" width="32" height="30" viewBox="0 0 32 30"><path d="M16 27 4 15a7 7 0 0 1 12-9 7 7 0 0 1 12 9z" fill="none" stroke="#222" stroke-width="2"/></svg>
  <svg class="abs" style="left:1025px;top:30px" width="40" height="34" viewBox="0 0 40 34"><path d="M2 4h6l4 18h20l4-13H10" fill="none" stroke="#222" stroke-width="2"/><circle cx="14" cy="28" r="2.5" fill="#222"/><circle cx="29" cy="28" r="2.5" fill="#222"/><circle cx="33" cy="7" r="7" fill="var(--orange)"/><text x="33" y="10" font-size="9" fill="#fff" text-anchor="middle" font-family="IBM Plex Sans,sans-serif">0</text></svg>
  <nav class="abs nav">
    <span class="active">HOME</span><span>ABOUT US</span><span>SERVICES</span><span>APPAREL</span><span>NUTRITION</span><span>BLOG</span><span>CONTACT US</span>
  </nav>
</header>

<section class="abs hero">
  <div class="ph" role="img" aria-label="Four folded printed t-shirts in red, green, blue and light blue" style="left:110px;top:30px;width:990px;height:420px;background:linear-gradient(90deg,#b5463f 0%,#8f9a3c 30%,#2a63a6 60%,#8db6d6 100%);opacity:.85;border-radius:4px"></div>
  <div class="hero-arrow" style="left:0"><svg width="10" height="14"><path d="M8 1 2 7l6 6" fill="none" stroke="#222" stroke-width="2"/></svg></div>
  <div class="hero-arrow" style="right:0"><svg width="10" height="14"><path d="M2 1l6 6-6 6" fill="none" stroke="#222" stroke-width="2"/></svg></div>
  <div class="abs hero-title" style="top:372px;font-size:60px">T SHIRTS</div>
  <div class="abs hero-title" style="top:445px;font-size:40px">GET <span style="background:var(--orange);padding:0 6px">30%</span> OFF</div>
  <div class="btn btn-ghost" style="left:536px;top:526px;width:128px;height:44px">Shop Now</div>
</section>

<div class="divider" style="top:781px"></div>
<h2 class="section-title" style="top:808px">Feature Products</h2>
<div class="filter" style="left:455px;width:62px;background:var(--orange);border-color:var(--orange);color:#fff">ALL</div>
<div class="filter" style="left:531px;width:93px">APPAREL</div>
<div class="filter" style="left:638px;width:106px">NUTRITION</div>

<svg class="abs" style="left:62px;top:1098px" width="16" height="24"><path d="M13 2 4 12l9 10" fill="none" stroke="#999" stroke-width="2"/></svg>
<svg class="abs" style="left:1117px;top:1098px" width="16" height="24"><path d="M3 2l9 10-9 10" fill="none" stroke="#999" stroke-width="2"/></svg>

<div class="card" style="left:346px;top:968px;width:216px;height:403px"></div>

<div class="ph" role="img" aria-label="Grey t-shirt" style="left:135px;top:995px;width:180px;height:185px;background:linear-gradient(#8a8a8a,#6c6c6c);border-radius:30px 30px 8px 8px"></div>
<div class="ph" role="img" aria-label="Orange supplement bottle" style="left:405px;top:990px;width:96px;height:192px;background:linear-gradient(90deg,#f07c1b,#ffb25c,#f07c1b);border-radius:20px"></div>
<div class="ph" role="img" aria-label="Red ringer t-shirt" style="left:605px;top:995px;width:200px;height:190px;background:linear-gradient(#b0242e,#8c1a22);border-radius:30px 30px 8px 8px"></div>
<div class="ph" role="img" aria-label="Black protein tub with red label" style="left:915px;top:998px;width:110px;height:185px;background:linear-gradient(#1d1d1d 0%,#1d1d1d 35%,#c2262e 35%,#c2262e 70%,#1d1d1d 70%);border-radius:18px"></div>

<div class="prod-name" style="left:110px;top:1204px">LOREM IPSUM</div>
<div class="prod-price" style="left:112px;top:1226px">$15.99<s>$35.99</s></div>
<div class="tag" style="left:184px;top:1265px">10% OFF</div>

<div class="prod-name" style="left:343px;top:1204px">LOREM IPSUM</div>
<div class="prod-price" style="left:345px;top:1226px">$25.99<s>$35.99</s></div>
<div class="tag" style="left:417px;top:1265px">10% OFF</div>
<div class="btn" style="left:405px;top:1314px;width:96px;height:34px;font-size:13px">Buy Now</div>

<div class="prod-name" style="left:595px;top:1204px">LOREM IPSUM</div>
<div class="prod-price" style="left:597px;top:1226px">$28.99<s>$35.99</s></div>
<div class="tag" style="left:669px;top:1265px">10% OFF</div>

<div class="prod-name" style="left:862px;top:1204px">LOREM IPSUM</div>
<div class="prod-price" style="left:864px;top:1226px">$32.99<s>$35.99</s></div>
<div class="tag" style="left:936px;top:1265px">10% OFF</div>

<section>
  <div class="ph" role="img" aria-label="Black supplement tub against a stormy sky" style="left:0;top:1442px;width:597px;height:448px;background:linear-gradient(135deg,#3a3a3a,#111 60%,#2b2b2b)"></div>
  <div class="ph" role="img" aria-label="Printed t-shirt on a hanger against a concrete wall" style="left:597px;top:1442px;width:603px;height:448px;background:linear-gradient(135deg,#9a9a9a,#c8c8c8 50%,#8a8a8a 90%,#8fc9c7)"></div>
  <div class="promo-title" style="left:348px;top:1620px">NUTRITION</div>
  <div class="promo-rule" style="left:348px;top:1667px"></div>
  <div class="promo-text" style="left:350px;top:1692px">Lorem Ipsum is simply dummy text of the printing and typesetting industry.</div>
  <div class="btn" style="left:350px;top:1790px;width:123px;height:38px;font-size:15px">Shop Now</div>

  <div class="promo-title" style="left:928px;top:1617px">T SHIRTS</div>
  <div class="promo-rule" style="left:928px;top:1664px"></div>
  <div class="promo-text" style="left:929px;top:1689px">Lorem Ipsum is simply dummy text of the printing and typesetting industry.</div>
  <div class="btn" style="left:929px;top:1786px;width:123px;height:38px;font-size:15px">Shop Now</div>
</section>

<div class="divider" style="top:1948px"></div>
<h2 class="section-title" style="top:1976px">Discounts</h2>
<div class="deal" style="left:131px;background:var(--red)">
  <h3>SAVE 10% OFF</h3>
  <p>Lorem Ipsum is simply dummy text of the printing and typesetting industry.</p>
  <div class="code">USE CODE : 5HJ45</div>
  <div class="btn" style="left:170px;top:232px;width:120px;height:36px">Shop Now</div>
</div>
<div class="deal" style="left:609px;background:var(--grey)">
  <h3>UPTO 75% OFF</h3>
  <p>Lorem Ipsum is simply dummy text of the printing and typesetting industry.</p>
  <div class="code">USE CODE : NU01TR</div>
  <div class="btn" style="left:170px;top:232px;width:120px;height:36px">Shop Now</div>
</div>

<section class="abs" style="left:0;top:2427px;width:1200px;height:596px;background:var(--soft)">
  <div class="divider" style="top:56px"></div>
  <h2 class="section-title" style="top:85px">New Products</h2>

  <div class="card" style="left:117px;top:163px;width:223px;height:368px"></div>
  <div class="ph" role="img" aria-label="Red t-shirt" style="left:155px;top:183px;width:148px;height:170px;background:#d8161c;border-radius:28px 28px 6px 6px"></div>
  <div class="prod-name" style="left:118px;top:398px">LOREM IPSUM</div>
  <div class="prod-price" style="left:118px;top:422px">$32.99<s>$35.99</s></div>
  <div class="btn" style="left:183px;top:468px;width:96px;height:34px;font-size:13px">Buy Now</div>

  <div class="card" style="left:365px;top:163px;width:223px;height:368px"></div>
  <div class="ph" role="img" aria-label="Black supplement tub with orange lid" style="left:428px;top:203px;width:96px;height:160px;background:linear-gradient(#f07c1b 0 14%,#1c1c1c 14%);border-radius:14px"></div>
  <div class="prod-name" style="left:366px;top:398px">LOREM IPSUM</div>
  <div class="prod-price" style="left:366px;top:422px">$32.99<s>$35.99</s></div>
  <div class="btn" style="left:431px;top:468px;width:96px;height:34px;font-size:13px">Buy Now</div>

  <div class="card" style="left:610px;top:163px;width:223px;height:368px"></div>
  <div class="ph" role="img" aria-label="Denim short-sleeve shirt" style="left:635px;top:195px;width:170px;height:160px;background:linear-gradient(#5f7fa6,#3d5c85);border-radius:26px 26px 6px 6px"></div>
  <div class="prod-name" style="left:611px;top:398px">LOREM IPSUM</div>
  <div class="prod-price" style="left:611px;top:422px">$32.99<s>$35.99</s></div>
  <div class="btn" style="left:676px;top:468px;width:96px;height:34px;font-size:13px">Buy Now</div>

  <div class="card" style="left:855px;top:163px;width:223px;height:368px"></div>
  <div class="ph" role="img" aria-label="Three black and gold vitamin jars" style="left:866px;top:210px;width:200px;height:145px;background:linear-gradient(#1a1a1a 0 20%,#b89b3a 20% 70%,#1a1a1a 70%);border-radius:10px"></div>
  <div class="prod-name" style="left:856px;top:398px">LOREM IPSUM</div>
  <div class="prod-price" style="left:856px;top:422px">$32.99<s>$35.99</s></div>
  <div class="btn" style="left:921px;top:468px;width:96px;height:34px;font-size:13px">Buy Now</div>
</section>

<section class="abs voucher" role="img" aria-label="Gift voucher illustration with a gift box, confetti and a coral side panel">
  <div class="voucher-frame"></div>
  <div class="voucher-amount">
    <span style="font-size:60px;vertical-align:top;line-height:120px">$ </span><span style="font-size:120px;line-height:120px">500</span>
  </div>
  <div class="abs" style="left:245px;top:372px;width:370px;text-align:center;color:var(--coral-deep);font-size:40px">VALUE</div>
  <div class="voucher-side" style="left:905px;top:505px;font-size:56px">GIFT VOUCHER</div>
  <div class="voucher-side" style="left:985px;top:360px;font-size:20px">DISCOUNT</div>
  <div class="voucher-side" style="left:1022px;top:420px;font-size:16px">Lorem ipsum dolor sit amet, consectetur.</div>
</section>

<div class="divider" style="top:3602px"></div>
<h2 class="section-title" style="top:3630px">Latest Blog</h2>
<article class="blog" style="left:131px">
  <div class="ph" role="img" aria-label="Golden supplement capsule on a mint background" style="left:10px;top:10px;width:271px;height:204px;background:radial-gradient(circle at 50% 50%,#e2c24a 0 25%,#8fd0bb 26%)"></div>
  <div class="date">22/10/2019</div><h4>LOREM IPSUM IS SIMPLY DUMMY</h4>
  <p>Lorem Ipsum is simply dummy text of the printing and types etting industry.</p><a>READ MORE</a>
</article>
<article class="blog" style="left:454px">
  <div class="ph" role="img" aria-label="Two men wearing grey t-shirts" style="left:10px;top:10px;width:271px;height:204px;background:linear-gradient(#8a8a8a,#4f4f4f)"></div>
  <div class="date">22/10/2019</div><h4>LOREM IPSUM IS SIMPLY DUMMY</h4>
  <p>Lorem Ipsum is simply dummy text of the printing and types etting industry.</p><a>READ MORE</a>
</article>
<article class="blog" style="left:777px">
  <div class="ph" role="img" aria-label="Woman in a white t-shirt and jeans on a city street" style="left:10px;top:10px;width:271px;height:204px;background:linear-gradient(90deg,#6b5a48,#d8d2c8 50%,#7a6a58)"></div>
  <div class="date">22/10/2019</div><h4>LOREM IPSUM IS SIMPLY DUMMY</h4>
  <p>Lorem Ipsum is simply dummy text of the printing and types etting industry.</p><a>READ MORE</a>
</article>

<section class="abs strip" style="left:0;top:4190px;width:1200px;height:118px;background:var(--strip)">
  <div class="abs" style="left:408px;top:0;width:410px;height:118px;background:var(--strip-mid)"></div>
  <svg class="abs" style="left:130px;top:40px" width="62" height="40" viewBox="0 0 62 40"><path d="M2 4h36v26H2zM38 12h12l10 10v8H38z" fill="none" stroke="#fff" stroke-width="2.5"/><circle cx="14" cy="33" r="5" fill="#4b4b4b" stroke="#fff" stroke-width="2.5"/><circle cx="48" cy="33" r="5" fill="#4b4b4b" stroke="#fff" stroke-width="2.5"/></svg>
  <h5 style="left:222px;top:36px">FREE SHIPPING</h5>
  <p style="left:222px;top:56px">Lorem Ipsum is simply dummy text of the print.</p>
  <svg class="abs" style="left:490px;top:34px" width="50" height="52" viewBox="0 0 50 52"><circle cx="28" cy="12" r="10" fill="none" stroke="#fff" stroke-width="2.5"/><path d="M4 42l10-10h14l-6 6h12l10-10" fill="none" stroke="#fff" stroke-width="2.5"/></svg>
  <h5 style="left:582px;top:36px">LOWEST PRICES</h5>
  <p style="left:582px;top:56px">Lorem Ipsum is simply dummy text of the print.</p>
  <svg class="abs" style="left:852px;top:40px" width="62" height="42" viewBox="0 0 62 42"><rect x="12" y="2" width="46" height="30" rx="4" fill="none" stroke="#fff" stroke-width="2.5"/><rect x="2" y="10" width="46" height="30" rx="4" fill="#4b4b4b" stroke="#fff" stroke-width="2.5"/><line x1="2" y1="19" x2="48" y2="19" stroke="#fff" stroke-width="4"/></svg>
  <h5 style="left:932px;top:36px">SECURE PAYMENT</h5>
  <p style="left:932px;top:56px">Lorem Ipsum is simply dummy text of the print.</p>
</section>

<footer class="abs" style="left:0;top:4308px;width:1200px;height:413px;background:var(--dark)">
  <div class="brand" style="left:130px;top:160px;font-size:46px;color:#fff"><span class="mark" style="background:#fff;width:34px;height:34px"></span>Vantor</div>
  <div class="foot-head" style="left:428px;top:54px">MENU</div>
  <ul class="foot-list" style="left:428px;top:92px"><li>HOME</li><li>ABOUT US</li><li>SERVICES</li><li>APPAREL</li><li>NUTRITION</li><li>BLOG</li><li>CONTACT US</li></ul>
  <div class="foot-head" style="left:582px;top:54px">CONTACT US</div>
  <div class="contact-row" style="top:96px"><span class="dot"><svg width="12" height="14"><path d="M6 13C2 8 1 6 1 5a5 5 0 0 1 10 0c0 1-1 3-5 8z" fill="#2e2e2e"/></svg></span><span>2250 Larkmoor Road<br>Bellfield, CA 90000</span></div>
  <div class="contact-row" style="top:158px"><span class="dot"><svg width="12" height="12"><path d="M2 1l3 1 1 3-2 1a7 7 0 0 0 3 3l1-2 3 1 1 3c-6 1-11-4-10-10z" fill="#2e2e2e"/></svg></span><span>Call Us<br>555.014.2288</span></div>
  <div class="contact-row" style="top:219px"><span class="dot"><svg width="14" height="10"><rect x="1" y="1" width="12" height="8" fill="none" stroke="#2e2e2e" stroke-width="1.5"/><path d="M1 1l6 5 6-5" fill="none" stroke="#2e2e2e" stroke-width="1.5"/></svg></span><span>E mail Us<br>info@vantorwear.com</span></div>
  <div class="foot-head" style="left:810px;top:54px">NEWSLETTER</div>
  <div class="field" style="top:97px">NAME</div>
  <div class="field" style="top:149px">E MAIL ID</div>
  <div class="btn" style="left:810px;top:205px;width:256px;height:40px">Signup</div>
  <div class="abs" style="left:125px;top:312px;width:950px;height:1px;background:#444"></div>
  <div class="abs" style="left:125px;top:348px;display:flex;align-items:center;gap:8px;color:#fff;font-size:14px;font-weight:700">FOLLOW US&nbsp;
    <span class="circle" style="background:var(--social)"></span>
    <span class="circle" style="background:var(--social)"></span>
    <span class="circle" style="background:var(--navy)"></span>
  </div>
  <div class="abs" style="left:800px;top:354px;width:272px;text-align:right;color:#fff;font-size:11px">Copyright © 2019 All Rights Reserved</div>
</footer>

</body>
</html>
```